Buch-/E-Book-Cover für Kinderbuch zum spielerischen Umgang zwischen Kind und Hund
Zielgruppe
Die Zielgruppe sind Kinder die lernen möchten mit Ihrem Hund besser zu spielen, verstehen und erziehen. Es ist ein Kinderbuch und das Buch soll dementsprechend 'kinderlicher' gestaltet sein.
Ich habe kein eigenes Konzept für das Cover mir derzeitig überlegt und ich werde die erstellten Cover bei meiner Zielgruppe testen und danach den Gewinner küren.
In diesem Buch handelt sich um ein Sachbuch zum Thema Hundeerziehung für Kinder. Ich möchte Ihnen die Inhaltsangabe, Vorwort und Buchrückseite mitteilen. Das Buch werde ich auf Lesekorb.de veröffentlichen. Außerdem möchte ich Ihnen die 2 größten Konkurrenten vorstellen.
Das Vorwort:
Vorwort
Der Hund ist für das Kind mehr als nur ein vierbeiniger Hausgenosse mit Kuschelfaktor, er ist ein echter Partner zum Spielen und Lernen. Mit den passenden Ideen gestaltet sich der Alltag mit dem Tier richtig spannend. Sowohl Kind als auch Hund entwickeln sich Schritt für Schritt weiter und wachsen immer mehr zusammen. Für Jungen und Mädchen gibt es vielfältige Möglichkeiten, sich mit ihrem Vierbeiner zu beschäftigen. Kreative Rollenspiele gehören ebenso dazu wie das Lernen von Kunststücken, das Training von Intelligenz und Geschicklichkeit und das Basteln schöner Spielsachen. Lassen Sie sich von diesem Buch inspirieren und von den Fähigkeiten Ihrer Kinder und Hunde überraschen!
Gliederung:
Einleitung und Grundlegendes
1. Warum spielen Hunde und Kinder?
Gemeinsamkeiten zwischen Kind und Welpe
Die Vorteile einer engen Hund-Kind-Beziehung
Kind und Hund – das absolute Dream-Team?
Welcher Hund passt zum Kind?
Voraussetzungen für sicheres Spielen
2. Kreative Spiele
Kreative Beschäftigung mit dem Hund – darf das sein?
Rollenspiele mit Hunden
Das richtige Alter für Rollenspiele
Beispiele für typische Rollenspiele im Kindesalter
Tierische Rollenspiele – vom Kind zum Hund
Eigene Kommandos erfi..
Aufgabenstellung
Der Titel vom Buch lautet: Komm zu uns! Wo Kleine den Vierbeiner kennen, führen und mit ihm toben dürfen.
Das sind die 2 größten Konkurrenten https://www.lesekorb.example/titel/4718
https://www.lesekorb.example/titel/5923
Das sind Cover auf dem Englisch sprachigen Markt die ich sehr gut finde
1. https://www.readbasket.example/item/8841
2. https://www.readbasket.example/item/3307

```html
<!DOCTYPE html>
<html lang="de">
<head>
<meta charset="utf-8">
<title>Komm zu uns! – Cover und Vorwort</title>
<link rel="stylesheet" href="https://fonts.googleapis.com/css2?family=Chewy&family=Sniglet:wght@800&display=swap">
<style>
  :root {
    --sky: #8dc0d8;
    --cloud: #e2eff6;
    --cloud-soft: #b4d6e7;
    --paper: #ffffff;
    --title-blue: #8cc1da;
    --ink: #4a2420;
  }
  * { box-sizing: border-box; margin: 0; padding: 0; }
  html, body { width: 1200px; height: 1200px; overflow: hidden; background: var(--paper); }
  .spread { position: relative; width: 1200px; height: 1200px; }
  .page {
    position: absolute; top: 160px; width: 533px; height: 828px;
    background: var(--sky); overflow: hidden;
  }
  .page--cover { left: 52px; }
  .page--foreword { left: 634px; }
  .sky-band {
    position: absolute; left: 0; top: 0; width: 100%; height: 95px;
    background: linear-gradient(180deg, var(--cloud) 0%, var(--cloud) 45%, var(--cloud-soft) 75%, var(--sky) 100%);
  }
  .title-band {
    position: absolute; left: 0; top: 92px; width: 100%; height: 210px;
    background: var(--paper); border-radius: 30px 8px 40px 12px;
  }
  .cover-title {
    position: absolute; left: 0; top: 92px; width: 100%;
    font-family: "Sniglet", "Chewy", sans-serif; font-weight: 800;
    color: var(--title-blue); text-align: center; text-transform: uppercase;
    font-size: 86px; line-height: 96px; padding-top: 8px; letter-spacing: -1px;
  }
  .cover-subtitle {
    position: absolute; left: 0; top: 325px; width: 100%;
    font-family: "Chewy", cursive; color: var(--ink);
    font-size: 21px; line-height: 31px; text-align: center; letter-spacing: 0.5px;
  }
  .cover-photo {
    position: absolute; left: 0; top: 415px; width: 100%; height: 413px;
    background: linear-gradient(90deg, #5a3a30 0%, #a89286 38%, #e9c9a8 58%, #d4453a 82%, #c23a30 100%);
  }
  .foreword-heading {
    position: absolute; left: 0; top: 82px; width: 100%;
    font-family: "Chewy", cursive; color: var(--ink);
    font-size: 54px; text-align: center; letter-spacing: 1px;
  }
  .foreword-text {
    position: absolute; left: 36px; top: 183px; width: 461px;
    font-family: "Chewy", cursive; color: var(--ink);
    font-size: 20px; line-height: 35.2px; text-align: center;
  }
</style>
</head>
<body>
<main class="spread">
  <section class="page page--cover" aria-label="Buchcover">
    <div class="sky-band" role="img" aria-label="Helle Wolken am Himmel"></div>
    <div class="title-band"></div>
    <h1 class="cover-title">Komm<br>zu uns!</h1>
    <p class="cover-subtitle">Wo Kleine den Vierbeiner kennen,<br>führen und mit ihm toben dürfen</p>
    <div class="cover-photo" role="img" aria-label="Foto: Ein Kind mit Weihnachtsmütze und ein Husky schauen sich Nase an Nase an"></div>
  </section>

  <section class="page page--foreword" aria-label="Vorwort">
    <div class="sky-band" role="img" aria-label="Helle Wolken am Himmel"></div>
    <h2 class="foreword-heading">Vorwort</h2>
    <p class="foreword-text">Der Hund ist für das Kind mehr als nur ein vierbeiniger Hausgenosse mit Kuschelfaktor, er ist ein echter Partner zum Spielen und Lernen. Mit den passenden Ideen gestaltet sich der Alltag mit dem Tier richtig spannend. Sowohl Kind als auch Hund entwickeln sich Schritt für Schritt weiter und wachsen immer mehr zusammen. Für Jungen und Mädchen gibt es vielfältige Möglichkeiten, sich mit ihrem Vierbeiner zu beschäftigen. Kreative Rollenspiele gehören ebenso dazu wie das Lernen von Kunststücken, das Training von Intelligenz und Geschicklichkeit und das Basteln schöner Spielsachen. Lassen Sie sich von diesem Buch inspirieren und von den Fähigkeiten Ihrer Kinder und Hunde überraschen!</p>
  </section>
</main>
</body>
</html>
```